Meridale Bed Company Needs Business Card

Looking for a very nice looking business card. Creative but not extravagant. We sell beds and pillows across the U.S. and need something professional but catchy. I have attached the logo.

Name : Devin Holt
Title : President
Phone : (800) 471-2960
Email: sleep@quilmora.com
Website: www.quilmora.com

Can be single-sided or double-sided
horizontal or vertical

Can use Blues/Greys

Target Market(s)

Mass Market

Industry/Entity Type

Retail

Contact Information for Business Card

Name : Devin Holt
Title : President
Phone : (800) 471-2960
Email: sleep@quilmora.com
Website: www.quilmora.com

Requirements
Must have
• Clean, Modern, Smooth
• Can use Blues/Greys
• On the other side without the information - have something simple like www.quilmora.com or our logo
Nice to have
• Surprise me
Should not have
• Nothing crazy, nothing cluttered

```html
<!DOCTYPE html>
<html lang="en">
<head>
<meta charset="utf-8">
<title>Quilmora Business Card</title>
<link href="https://fonts.googleapis.com/css2?family=Arimo:wght@400;700&display=swap" rel="stylesheet">
<style>
  :root {
    --backdrop: #2b2c2e;
    --card-white: #ffffff;
    --card-white-shade: #eef0f1;
    --brand-blue: #2ba3d9;
    --brand-blue-deep: #1f8fc8;
    --text-light: #ffffff;
    --text-soft: rgba(255, 255, 255, 0.88);
    --rule: rgba(255, 255, 255, 0.45);
  }
  * { box-sizing: border-box; margin: 0; padding: 0; }
  html, body {
    width: 1200px;
    height: 843px;
    overflow: hidden;
    background: var(--backdrop);
    font-family: "Arimo", Arial, sans-serif;
  }
  .card-set {
    position: relative;
    width: 1200px;
    height: 843px;
  }
  .card {
    position: absolute;
    top: 267px;
    width: 540px;
    height: 309px;
    border-radius: 3px;
    overflow: hidden;
  }
  .card--front {
    left: 40px;
    background: linear-gradient(160deg, var(--card-white) 55%, var(--card-white-shade) 100%);
  }
  .card--back {
    left: 620px;
    background: linear-gradient(170deg, var(--brand-blue) 0%, var(--brand-blue-deep) 100%);
  }
  .wordmark {
    font-family: "Arimo", Arial, sans-serif;
    font-weight: 400;
    letter-spacing: 2px;
    line-height: 1;
  }
  .card--front .wordmark {
    position: absolute;
    left: 0;
    right: 0;
    top: 118px;
    text-align: center;
    font-size: 64px;
    color: var(--brand-blue);
  }
  .card--back .wordmark {
    position: absolute;
    right: 34px;
    top: 48px;
    font-size: 56px;
    color: var(--text-light);
  }
  .contact-block {
    position: absolute;
    left: 30px;
    right: 30px;
    top: 188px;
    color: var(--text-light);
  }
  .contact-name {
    font-size: 18px;
    font-weight: 700;
  }
  .contact-title {
    font-weight: 400;
    font-size: 15px;
    color: var(--text-soft);
  }
  .contact-lines {
    margin-top: 12px;
    display: flex;
    gap: 14px;
    font-size: 13px;
    color: var(--text-soft);
  }
  .contact-label { font-weight: 700; color: var(--text-light); }
  .contact-rule {
    margin-top: 10px;
    height: 1px;
    background: var(--rule);
  }
</style>
</head>
<body>
  <main class="card-set">
    <section class="card card--front" aria-label="Card front">
      <div class="wordmark">quilmora</div>
    </section>

    <section class="card card--back" aria-label="Card back">
      <div class="wordmark">quilmora</div>
      <div class="contact-block">
        <p class="contact-name">Devin Holt <span class="contact-title">- President</span></p>
        <div class="contact-lines">
          <span><span class="contact-label">P:</span> (800) 471-2960</span>
          <span><span class="contact-label">E:</span> sleep@quilmora.com</span>
          <span><span class="contact-label">W:</span> www.quilmora.com</span>
        </div>
        <div class="contact-rule"></div>
      </div>
    </section>
  </main>
</body>
</html>
```